KRV Photography Business Card Design

I would like a business card designed in the shape of a camera.
Would like to see various camera designs. Would like to see what the card looks like in different colors. Would like to see which logo looks better on the various camera designs so please show me some with the white logo and some with the black logo. If you need a different file formats please let me know.
Project Deadline Extended Reason: My grandfather passed away and dealing with funeral plans so need to extend deadline. Added Tuesday, March 1, 2016
Project Deadline Extended
Reason: I just got back from out of town. My grandfather's passing was the primary focus for me these past few weeks and the funeral is over so now I will concentrate on picking my business card design. I really appreciate each designer who has taken the time to submit a design. Your effort has not gone unnoticed. I look forward to seeing more amazing designs.
Business
Contact Information for Business Card
Dorine
555-418-2706
https://www.facebook.com/krvphotographyfreelance/
MonaDorine@krv-photography.example

```html
<!DOCTYPE html>
<html lang="en">
<head>
<meta charset="utf-8">
<title>KRV Photography – Business Card</title>
<link href="https://fonts.googleapis.com/css2?family=Marcellus&family=Open+Sans:wght@400;700&display=swap" rel="stylesheet">
<style>
  :root {
    --backdrop: #bdbec0;
    --card: #000000;
    --gold: #d4a437;
    --amber: #c8862a;
    --white: #ffffff;
    --rule-light: #d9d9d9;
  }
  * { margin: 0; padding: 0; box-sizing: border-box; }
  html, body {
    width: 1200px; height: 927px; overflow: hidden;
    background: var(--backdrop);
  }
  .stage { position: relative; width: 1200px; height: 927px; }

  .camera-card {
    position: absolute; top: 297px; width: 522px; height: 332px;
    filter: drop-shadow(0 4px 8px rgba(0,0,0,.45));
  }
  .camera-card--gold { left: 54px; --accent: var(--amber); --rule: var(--amber); }
  .camera-card--white { left: 624px; --accent: var(--white); --rule: var(--rule-light); }

  .card-body {
    position: absolute; left: 0; top: 20px; width: 522px; height: 312px;
    background: var(--card); border-radius: 18px;
  }
  .shutter-button {
    position: absolute; left: 68px; top: 14px; width: 62px; height: 12px;
    background: var(--card); border-radius: 6px 6px 0 0;
  }
  .viewfinder {
    position: absolute; left: 368px; top: 0; width: 100px; height: 26px;
    background: var(--card); border-radius: 9px 9px 0 0;
  }

  .brand-mark {
    position: absolute; left: 104px; top: 26px; width: 78px; height: 78px;
    border-radius: 50%; background: var(--gold);
  }
  .brand-name {
    position: absolute; left: 24px; top: 116px;
    font-family: "Marcellus", serif; font-size: 24px; letter-spacing: .3px;
    color: var(--gold); white-space: nowrap;
  }

  .name-row {
    position: absolute; left: 0; right: 26px; top: 226px;
    display: flex; align-items: center;
  }
  .name-rule {
    flex: 1 1 auto; height: 2px; margin-right: 4px;
    background: var(--rule);
  }
  .person-name {
    flex: none; white-space: nowrap;
    font-family: "Open Sans", sans-serif; font-weight: 700; font-size: 20px;
    letter-spacing: 2px; color: var(--accent); line-height: 24px;
  }
  .contact-list {
    position: absolute; right: 26px; top: 258px; list-style: none;
    font-family: "Open Sans", sans-serif; font-size: 12.5px; letter-spacing: .8px;
    color: var(--accent); text-align: right; line-height: 15.5px;
  }
  .contact-list li { display: flex; align-items: center; justify-content: flex-end; gap: 7px; white-space: nowrap; }
  .contact-icon { width: 10px; height: 10px; flex: none; }
</style>
</head>
<body>
<main class="stage">

  <section class="camera-card camera-card--gold">
    <div class="shutter-button"></div>
    <div class="viewfinder"></div>
    <div class="card-body">
      <div class="brand-mark"></div>
      <p class="brand-name">KRV PHOTOGRAPHY</p>
      <div class="name-row">
        <div class="name-rule"></div>
        <h1 class="person-name">THEO MARSDEN</h1>
      </div>
      <ul class="contact-list">
        <li>+330 5550-1482
          <svg class="contact-icon" viewBox="0 0 10 10" fill="none" stroke="currentColor" stroke-width="1.1"><path d="M2 1 L3.5 1 L4 3 L3 4 Q4.3 6.2 6 7 L7 6 L9 6.5 L9 8 Q8.5 9 7.5 9 Q1 8 1 2.5 Q1 1.2 2 1 Z"/></svg>
        </li>
        <li>theo@marsdenmail.example
          <svg class="contact-icon" viewBox="0 0 10 10" fill="none" stroke="currentColor" stroke-width="1.1"><rect x="0.8" y="2" width="8.4" height="6.2"/><path d="M0.8 2 L5 5.3 L9.2 2"/></svg>
        </li>
      </ul>
    </div>
  </section>

  <section class="camera-card camera-card--white">
    <div class="shutter-button"></div>
    <div class="viewfinder"></div>
    <div class="card-body">
      <div class="brand-mark"></div>
      <p class="brand-name">KRV PHOTOGRAPHY</p>
      <div class="name-row">
        <div class="name-rule"></div>
        <h1 class="person-name">THEO MARSDEN</h1>
      </div>
      <ul class="contact-list">
        <li>+330 5550-1482
          <svg class="contact-icon" viewBox="0 0 10 10" fill="none" stroke="currentColor" stroke-width="1.1"><path d="M2 1 L3.5 1 L4 3 L3 4 Q4.3 6.2 6 7 L7 6 L9 6.5 L9 8 Q8.5 9 7.5 9 Q1 8 1 2.5 Q1 1.2 2 1 Z"/></svg>
        </li>
        <li>theo@marsdenmail.example
          <svg class="contact-icon" viewBox="0 0 10 10" fill="none" stroke="currentColor" stroke-width="1.1"><rect x="0.8" y="2" width="8.4" height="6.2"/><path d="M0.8 2 L5 5.3 L9.2 2"/></svg>
        </li>
      </ul>
    </div>
  </section>

</main>
</body>
</html>
```